Product Designer Business Card

Small product design, engineering and prototyping firm in need of a clean, professional business card design. To support our 3D design and drawing services, we offer 3D printing, molding, and casting of plastics, silicones, resins, etc. Our logo can still be modified/changed if necessary. The red/orange color is preferred, but may be substituted with blue or green, potentially. Either way, the colour of the logo should be match/compliment colors used throughout the design. One thought is to have the logo/contact info on one side, with the other side describing services offered, like with a small icon of 3D printer, molding, casting, and computer with a 3D model on-screen.
Industry/Entity Type
Mechanical Engineering
Contact Information for Business Card
Company: Kelvar Design
Phone: 613-582-9047
Email: mark@kelvardesign.ca

```html
<!DOCTYPE html>
<html lang="en">
<head>
<meta charset="utf-8">
<title>Kelvar Design Business Card</title>
<link rel="stylesheet" href="https://fonts.googleapis.com/css2?family=Open+Sans:wght@400;600;700&display=swap">
<style>
  :root {
    --bg: #3a3330;
    --card: #111111;
    --card-edge: #1c1c1c;
    --accent: #e2381b;
    --text: #f2f2f2;
    --muted: #bdbdbd;
    --divider: #2a2a2a;
  }
  * { box-sizing: border-box; margin: 0; padding: 0; }
  html, body { width: 1200px; height: 844px; overflow: hidden; }
  body {
    background: var(--bg);
    font-family: "Open Sans", Arial, sans-serif;
    position: relative;
  }
  .card {
    position: absolute;
    top: 272px;
    width: 525px;
    height: 300px;
    background: var(--card);
    border: 1px solid var(--card-edge);
    border-radius: 4px;
    box-shadow: 0 14px 30px rgba(0,0,0,0.45);
  }
  .card--front { left: 50px; display: flex; }
  .card--back { left: 625px; }

  .front__brand {
    width: 50%;
    display: flex;
    align-items: center;
    justify-content: center;
    gap: 12px;
    border-right: 1px solid var(--divider);
  }
  .brand-dot {
    width: 26px; height: 26px;
    border-radius: 50%;
    background: var(--accent);
  }
  .brand-name {
    font-size: 26px;
    font-weight: 700;
    color: var(--accent);
    letter-spacing: 1px;
  }
  .front__contact {
    width: 50%;
    padding: 74px 0 0 30px;
  }
  .person-name { color: var(--accent); font-size: 19px; font-weight: 700; line-height: 1.1; }
  .person-title { color: var(--text); font-size: 14px; margin-bottom: 22px; }
  .contact-list { list-style: none; }
  .contact-list li {
    display: flex; align-items: center; gap: 9px;
    color: var(--text); font-size: 15px; line-height: 1.45;
  }
  .contact-list svg { width: 14px; height: 14px; flex: none; }

  .back__brand {
    display: flex; align-items: center; justify-content: center; gap: 12px;
    margin-top: 62px;
  }
  .back__brand .brand-dot { background: var(--text); }
  .back__brand .brand-name { color: var(--text); font-size: 30px; }
  .services {
    list-style: none;
    display: flex; justify-content: center; gap: 30px;
    margin-top: 46px;
  }
  .service { display: flex; flex-direction: column; align-items: center; gap: 8px; width: 80px; }
  .service svg { width: 46px; height: 46px; }
  .service span { color: var(--text); font-size: 12px; font-weight: 600; }
</style>
</head>
<body>
  <section class="card card--front">
    <div class="front__brand">
      <span class="brand-dot"></span>
      <span class="brand-name">Kelvar Design</span>
    </div>
    <div class="front__contact">
      <p class="person-name">Daniel Reyes</p>
      <p class="person-title">Managing Director</p>
      <ul class="contact-list">
        <li>
          <svg viewBox="0 0 16 16"><rect x="1" y="1" width="14" height="14" rx="2" fill="none" stroke="#e2381b" stroke-width="1.5"/><path d="M5 4 L7 4 L7.5 6.5 L6.3 7.3 Q7.5 9.5 9 10 L9.8 8.8 L12 9.5 L12 11.5 Q8 12 5.5 8.5 Q4.3 6.5 5 4Z" fill="#e2381b"/></svg>
          613-582-9047
        </li>
        <li>
          <svg viewBox="0 0 16 16"><rect x="1" y="3" width="14" height="10" fill="#e2381b"/><path d="M1 3 L8 9 L15 3" fill="none" stroke="#111" stroke-width="1.3"/></svg>
          mark@kelvardesign.ca
        </li>
        <li>
          <svg viewBox="0 0 16 16" fill="none" stroke="#e2381b" stroke-width="1.4"><circle cx="8" cy="8" r="6.5"/><ellipse cx="8" cy="8" rx="3" ry="6.5"/><path d="M1.5 8 H14.5 M2.5 4.8 H13.5 M2.5 11.2 H13.5"/></svg>
          www.kelvardesign.ca
        </li>
      </ul>
    </div>
  </section>

  <section class="card card--back">
    <div class="back__brand">
      <span class="brand-dot"></span>
      <span class="brand-name">Kelvar</span>
    </div>
    <ul class="services">
      <li class="service">
        <svg viewBox="0 0 46 46" fill="none" stroke="#f2f2f2" stroke-width="3"><rect x="4" y="4" width="38" height="38" rx="3"/><path d="M10 14 H36 M18 14 V22 M14 34 H32 M12 40 H34"/><rect x="14" y="22" width="8" height="5" fill="#f2f2f2"/></svg>
        <span>3D Printer</span>
      </li>
      <li class="service">
        <svg viewBox="0 0 46 46" fill="none" stroke="#f2f2f2" stroke-width="3"><rect x="12" y="3" width="22" height="8"/><path d="M23 11 V17"/><rect x="10" y="17" width="26" height="10"/><rect x="10" y="31" width="26" height="8"/><path d="M6 43 H40"/></svg>
        <span>Molding</span>
      </li>
      <li class="service">
        <svg viewBox="0 0 46 46" fill="none" stroke="#f2f2f2" stroke-width="3"><rect x="4" y="6" width="14" height="14"/><path d="M18 12 Q30 8 34 22"/><path d="M26 28 L38 28 L40 40 L24 40Z" fill="#f2f2f2"/><path d="M4 42 H44"/></svg>
        <span>Casting</span>
      </li>
      <li class="service">
        <svg viewBox="0 0 46 46" fill="none" stroke="#f2f2f2" stroke-width="3"><rect x="3" y="5" width="40" height="28" rx="2"/><path d="M23 33 V39 M14 41 H32"/><path d="M23 11 L31 15 L31 24 L23 28 L15 24 L15 15Z M15 15 L23 19 L31 15 M23 19 V28" stroke-width="2"/></svg>
        <span>3d Model</span>
      </li>
    </ul>
  </section>
</body>
</html>
```